Timber Crest Construction Needs business card

Hey we are in need of business card designs. I have upload our logo as a guideline, but free feel to run with it or come up with something unique.
Pls have fun with it and be creative. the name says it all!
i will give some directions after i see a few entries..
Updates
Logo source file has been uploaded..
Hey because of the logo is so colourful already.
Can we have a few submissions with less colour.
Also we are looking for clever/hidden/descriptive business card.

```html
<!DOCTYPE html>
<html lang="en">
<head>
<meta charset="utf-8">
<title>Timber Crest Construction – Business Card</title>
<link href="https://fonts.googleapis.com/css2?family=Open+Sans:wght@400;600;700&display=swap" rel="stylesheet">
<style>
  :root {
    --backdrop: #e9e7e4;
    --card: #ffffff;
    --ink-grey: #5f6466;
    --title-blue: #4a9fe0;
    --lime: #66ff00;
    --swoosh: #5f6466;
    --contact-text: #ffffff;
  }
  * { box-sizing: border-box; margin: 0; padding: 0; }
  html, body {
    width: 1200px; height: 470px; overflow: hidden;
    background: var(--backdrop);
    font-family: "Open Sans", Arial, sans-serif;
  }
  .canvas {
    position: relative; width: 1200px; height: 470px;
    display: flex; align-items: center; justify-content: center; gap: 60px;
  }
  .card {
    position: relative; width: 520px; height: 300px;
    background: var(--card);
    box-shadow: 0 4px 14px rgba(0,0,0,0.18);
    overflow: hidden;
  }
  .card-front .wave { position: absolute; inset: 0; width: 100%; height: 100%; }
  .brand {
    display: flex; align-items: center; gap: 10px;
    color: var(--ink-grey); font-weight: 700; letter-spacing: 0.5px;
  }
  .brand-square { background: var(--ink-grey); flex: none; }
  .card-front .brand {
    position: absolute; top: 70px; right: 34px; font-size: 22px;
  }
  .card-front .brand-square { width: 26px; height: 26px; }
  .holder { position: absolute; left: 38px; top: 100px; }
  .holder-name { color: var(--ink-grey); font-weight: 700; font-size: 19px; }
  .holder-title { color: var(--title-blue); font-weight: 700; font-size: 19px; margin-top: 2px; }
  .contacts {
    position: absolute; left: 38px; top: 190px; list-style: none;
    color: var(--contact-text); font-size: 12.5px; line-height: 19px;
  }
  .contacts li { display: flex; align-items: center; gap: 6px; }
  .contacts svg { width: 11px; height: 11px; flex: none; }
  .card-back { display: flex; align-items: center; justify-content: center; }
  .card-back .brand { font-size: 28px; }
  .card-back .brand-square { width: 34px; height: 34px; }
</style>
</head>
<body>
<main class="canvas">
  <section class="card card-front" aria-label="Business card front">
    <svg class="wave" viewBox="0 0 520 300" preserveAspectRatio="none" aria-hidden="true">
      <path d="M0,185 C120,150 260,175 380,160 C450,150 500,135 520,118 L520,300 L0,300 Z" fill="var(--lime)"/>
      <path d="M60,168 C180,150 300,165 400,148 C460,138 500,120 520,100 L520,118 C495,140 455,155 390,163 C290,175 170,160 60,168 Z" fill="var(--swoosh)"/>
    </svg>
    <div class="brand">
      <span class="brand-square"></span>
      <span>TIMBER CREST CONSTRUCTION</span>
    </div>
    <div class="holder">
      <p class="holder-name">Your Name</p>
      <p class="holder-title">Title</p>
    </div>
    <ul class="contacts">
      <li><svg viewBox="0 0 12 12"><circle cx="6" cy="6" r="5.3" fill="none" stroke="#fff" stroke-width="1.2"/><path d="M4,3 L5.2,3 L5.6,4.6 L4.9,5.2 C5.3,6.1 5.9,6.8 6.8,7.2 L7.4,6.5 L9,6.9 L9,8.1 C6,8.4 3.6,6 4,3 Z" fill="#fff"/></svg>0400 555 018</li>
      <li><svg viewBox="0 0 12 12"><circle cx="6" cy="6" r="5.3" fill="none" stroke="#fff" stroke-width="1.2"/><path d="M4,3 L5.2,3 L5.6,4.6 L4.9,5.2 C5.3,6.1 5.9,6.8 6.8,7.2 L7.4,6.5 L9,6.9 L9,8.1 C6,8.4 3.6,6 4,3 Z" fill="#fff"/></svg>0400 555 018</li>
      <li><svg viewBox="0 0 12 12"><rect x="1" y="2.5" width="10" height="7" fill="#fff"/><path d="M1,2.5 L6,6.5 L11,2.5" fill="none" stroke="var(--lime)" stroke-width="1"/></svg>info@tcconstruction.com</li>
      <li><svg viewBox="0 0 12 12"><circle cx="6" cy="6" r="5" fill="#fff"/><path d="M1,6 H11 M6,1 C3.5,3.5 3.5,8.5 6,11 M6,1 C8.5,3.5 8.5,8.5 6,11" fill="none" stroke="var(--lime)" stroke-width="0.8"/></svg>www.tcconstruction.com</li>
      <li>Street Name City Name, State Zipcode</li>
    </ul>
  </section>

  <section class="card card-back" aria-label="Business card back">
    <div class="brand">
      <span class="brand-square"></span>
      <span>TIMBER CREST CONSTRUCTION</span>
    </div>
  </section>
</main>
</body>
</html>
```